Property management company looking for modern card design

We at Blue Heron Partners provides property management services for its residential and commercial properties, with expertise in all categories of multifamily, industrial and office projects throughout California.

We need a business card design that is professional and modern designed business card. In our field, clients get hundreds of business cards, we would like our card to stand out.

Please avoid small print.

Target Market(s)

Professionals and high end clients

Industry/Entity Type

Financial Planning

Contact Information for Business Card

Company Name: Blue Heron Partners, Name, email, license #, phone number, website blueheronpartners.com

Font styles to use
Sans Serif

Requirements
Must have
• The card design needs to be adaptable because there is a possibly we will be expanding into different sectors other than real estate. The card design should be focused on financial planning and asset management.
Nice to have
• Modern and simple business card. Eye catching. Non-standard size/shaped cards would be great.
• blueheronpartners.com
Should not have
• Too many bright color or any pictures or shapes of real estate stuff.

```html
<!DOCTYPE html>
<html lang="en">
<head>
<meta charset="utf-8">
<title>Blue Heron Partners – Business Card</title>
<link rel="stylesheet" href="https://fonts.googleapis.com/css2?family=Montserrat:wght@300;400;500;700&display=swap">
<style>
  :root {
    --page-bg: #e9e6e2;
    --card-dark: #333333;
    --card-light: #ffffff;
    --accent: #c9302c;
    --ink: #222222;
    --ink-soft: #444444;
    --on-dark: #ffffff;
    --rule-on-dark: #8a8a8a;
    --rule-on-light: #bdbdbd;
  }
  * { margin: 0; padding: 0; box-sizing: border-box; }
  html, body {
    width: 1200px; height: 1000px; overflow: hidden;
    background: var(--page-bg);
    font-family: "Montserrat", sans-serif;
  }
  .canvas { position: relative; width: 1200px; height: 1000px; }
  .card {
    position: absolute; left: 288px; width: 625px; height: 357px;
    border-radius: 28px;
    box-shadow: 0 6px 14px rgba(0,0,0,0.25);
  }
  .card--front { top: 140px; background: var(--card-dark); }
  .card--back { top: 532px; background: var(--card-light); text-align: center; }

  .wordmark {
    position: absolute; top: 134px; left: 0; right: 0;
    text-align: center; color: var(--on-dark);
    font-weight: 400; font-size: 52px; letter-spacing: 1px; line-height: 1;
  }
  .tagline-row {
    position: absolute; top: 200px; left: 122px; right: 122px;
    display: flex; align-items: center; gap: 12px;
  }
  .tagline-row .rule { flex: 1; height: 1px; background: var(--rule-on-dark); }
  .tagline {
    color: var(--on-dark); font-weight: 400; font-size: 25px; line-height: 1;
  }

  .brand-dot {
    position: absolute; left: 264px; top: 42px;
    width: 96px; height: 96px; border-radius: 50%;
    background: var(--accent);
  }
  .holder-name {
    position: absolute; top: 166px; left: 0; right: 0;
    color: var(--accent); font-weight: 700; font-size: 23px;
  }
  .holder-role {
    position: absolute; top: 193px; left: 0; right: 0;
    color: var(--ink-soft); font-size: 14px; font-weight: 500;
  }
  .divider {
    position: absolute; top: 222px; left: 184px; width: 256px; height: 2px;
    background: linear-gradient(90deg, transparent, var(--rule-on-light) 50%, transparent);
  }
  .contact {
    position: absolute; left: 0; right: 0;
    color: var(--ink); font-size: 14.5px; font-weight: 400;
  }
  .contact--license { top: 238px; }
  .contact--lines { top: 263px; }
  .contact--web { top: 288px; }
  .label { color: var(--accent); }
  .sep { margin: 0 8px; }
</style>
</head>
<body>
<div class="canvas">
  <section class="card card--front" aria-label="Card front">
    <div class="wordmark">BLUE HERON</div>
    <div class="tagline-row">
      <span class="rule"></span>
      <span class="tagline">PARTNERS</span>
      <span class="rule"></span>
    </div>
  </section>

  <section class="card card--back" aria-label="Card back">
    <div class="brand-dot"></div>
    <div class="holder-name">Daniel Reyes</div>
    <div class="holder-role">President</div>
    <div class="divider"></div>
    <div class="contact contact--license">License: #7081946</div>
    <div class="contact contact--lines"><span class="label">P</span>: 555-0142-7730<span class="sep">|</span><span class="label">E</span>: info@blueheronpartners.com</div>
    <div class="contact contact--web">www.blueheronpartners.com</div>
  </section>
</div>
</body>
</html>
```